Wordpress Web Design & Coding for velcorahealth.ca

We need a website for a new investment company that is visually grabbing and vibrant. We would like to see a web page that displays trust, growth and confidence. Needs to be responsive and mobile friendly for all browsers and coded for both Android & IOS.

Open to the number of pages and menu items. I selected 4 but if you feel the layout would work better with less I am open to this. Need to sell the people (management team/related businesses) and then show where the invested money will be going (upcoming projects).

Company Info:

Vel Cora is an investment company put together by a group of seasoned business professionals who have come together to combine decades of success in the real estate development, management, financing and medical services. The company will be a full service company offering turn key solutions for medical professionals.

Vel-Cora will focus on providing a full range of services via a group of distinct companies to deliver newly emerging needs of the medical community. The end goal will be to create complete solutions for individuals in the medical community. Our group has experience and success with the conceptualization, construction and financing of medical and dental clinic spaces. Vel-Cora Solutions will be established to accommodate all areas of the development and creation of clinics for medical professionals from building construction to equipment financing and administrations.

You can mention these companies and take photos from their websites. You can also use stock photos.

Our construction partner:
https://318bld.com/projects/

Our equipment leasing partner:
https://www.norvixa.com/

Our Management Team and medical partners

Gil Parish
https://www.ourfirmstance.ca/

Dietmar Vellasquin
https://www.gshdentalservices.com/about-us

PROPOSED PROJECTS (see attachment for details)
Pinegrove Business Park
Holtmere Business Park
Mt. Corwin Ridge Professional

Target Market(s)

Investors

Industry/Entity Type

Investment

Coding

Coded - Design and coding required

Number of Pages Required

4 page

Font styles to use
Sans Serif

Requirements
Must have
• Wordpress – must be both desktop and mobile friendly with fast page load speed
Ability to edit after ourselves in Wordpress
Attractive home page with logo etc.
Logo colours are: for the blue the pantone color is #0355a3
and for the green is #8cc63f

Sections, about us, what we do/services we provide, contact us

```html
<!DOCTYPE html>
<html lang="en">
<head>
<meta charset="utf-8">
<title>Vel-Cora Solutions</title>
<link rel="stylesheet" href="https://fonts.googleapis.com/css2?family=Raleway:wght@400;500;600&family=Roboto:wght@700;900&display=swap">
<style>
:root{
  --blue:#0355a3;
  --blue-footer:#0b58a8;
  --green:#8cc63f;
  --ink:#222;
  --muted:#6c6c6c;
  --nav:#3b3b3b;
  --line:#b9bcc1;
}
*{box-sizing:border-box;margin:0;padding:0}
html,body{width:1200px;height:2846px;overflow:hidden}
body{position:relative;background:#fff;font-family:"Raleway",sans-serif;color:var(--ink)}
.abs{position:absolute}
a{text-decoration:none}

/* header */
.site-header{position:absolute;left:0;top:0;width:1200px;height:107px;background:#fff;z-index:3}
.brand{position:absolute;left:112px;top:40px;display:flex;align-items:center;gap:9px}
.brand-mark{width:16px;height:16px;background:var(--green);border-radius:50%}
.brand-name{font-weight:600;font-size:25px;color:var(--blue);line-height:1.05}
.brand-name small{display:block;font-size:13px;letter-spacing:2px}
.main-nav{position:absolute;top:51px;left:383px;font-size:16px;color:var(--nav)}
.main-nav a{color:inherit;position:absolute;white-space:nowrap}
.main-nav .active{color:var(--blue)}
.btn{display:flex;align-items:center;justify-content:center;border-radius:26px;background:var(--green);color:#fff;font-size:16px;box-shadow:0 2px 5px rgba(0,0,0,.15)}
.login{left:935px;top:36px;width:155px;height:51px;gap:8px}

/* hero */
.hero-photo{left:0;top:107px;width:1200px;height:660px;
  background:
    radial-gradient(ellipse 380px 260px at 140px 120px,rgba(240,236,226,.9),transparent 70%),
    radial-gradient(ellipse 300px 420px at 1080px 200px,rgba(40,46,56,.85),transparent 75%),
    radial-gradient(ellipse 520px 200px at 700px 600px,rgba(232,238,246,.95),transparent 75%),
    radial-gradient(ellipse 260px 160px at 330px 470px,rgba(70,92,120,.7),transparent 75%),
    linear-gradient(115deg,#b9b3a4 0%,#8d98a5 35%,#a9b4c1 55%,#6d7784 78%,#3a4049 100%);}
.hero-box{left:262px;top:311px;width:731px;height:237px;background:rgba(70,150,215,.55);text-align:center;color:#fff}
.hero-box h1{font-family:"Roboto",sans-serif;font-weight:900;font-size:59px;margin-top:24px;line-height:1}
.hero-box p{font-size:16px;line-height:27px;margin:12px auto 0;width:540px}
.get-started{left:550px;top:465px;width:154px;height:51px}
.dots{left:981px;top:655px;display:flex;gap:9px}
.dots span{width:14px;height:14px;border:1.5px solid #fff;border-radius:50%}
.dots .on{background:var(--blue);border-color:var(--blue)}

/* about */
.about-bg{left:0;top:767px;width:1200px;height:589px;background:linear-gradient(180deg,#fff 0%,#f7f8f9 60%,#f1f2f4 100%)}
.about-photo{left:135px;top:867px;width:390px;height:390px;border-radius:50%;box-shadow:0 3px 8px rgba(0,0,0,.12);
  background:
    radial-gradient(circle at 70% 35%,rgba(216,170,140,.8),transparent 30%),
    radial-gradient(ellipse 200px 90px at 45% 85%,rgba(40,120,220,.75),transparent 70%),
    radial-gradient(ellipse 160px 70px at 45% 62%,rgba(60,140,230,.55),transparent 70%),
    linear-gradient(160deg,#eef1f4 0%,#c9d3de 45%,#9fb0c4 75%,#7388a3 100%);}
.about-ring{left:125px;top:864px}
h2.section-title{font-family:"Roboto",sans-serif;font-weight:900;font-size:44px;color:#222;line-height:1}
.about-title{left:600px;top:896px}
.about-text{left:601px;top:958px;width:442px;font-size:15.2px;line-height:34.3px;color:var(--muted);text-align:justify}
.read-more{left:600px;top:1174px;width:154px;height:51px}

/* services */
.services{left:0;top:1355px;width:1200px;height:552px;background:linear-gradient(180deg,#eceef1,#f6f7f8)}
.services-title{left:0;width:1200px;top:1457px;text-align:center}
.service-card{top:1518px;width:317px;height:248px;box-shadow:0 2px 6px rgba(0,0,0,.15)}
.card-estate{left:110px;background:
    radial-gradient(ellipse 140px 70px at 60% 75%,rgba(70,60,55,.75),transparent 70%),
    radial-gradient(ellipse 120px 90px at 75% 20%,rgba(120,140,100,.8),transparent 70%),
    linear-gradient(180deg,#dfe3dc 0%,#b9c0b2 45%,#6e6a62 80%,#4c4843 100%);}
.card-mgmt{left:440px;background:
    radial-gradient(ellipse 120px 80px at 70% 60%,rgba(230,238,246,.95),transparent 70%),
    radial-gradient(ellipse 90px 120px at 85% 20%,rgba(240,210,150,.9),transparent 70%),
    linear-gradient(120deg,#3b3a36 0%,#6d5d48 40%,#a88c66 70%,#d8c8a8 100%);}
.card-finance{left:770px;background:
    radial-gradient(circle at 55% 65%,rgba(110,116,124,.8),transparent 18%),
    radial-gradient(ellipse 160px 60px at 40% 20%,rgba(255,255,255,.9),transparent 70%),
    linear-gradient(150deg,#f1f3f5 0%,#d7dce2 50%,#aab2bb 100%);}
.service-label{top:1786px;width:317px;text-align:center;font-size:16px;font-weight:500;color:#222}
.arrow{top:1638px;width:38px;height:38px}

/* contact */
.contact-bg{left:0;top:1907px;width:1200px;height:653px;background:linear-gradient(160deg,#fff 0%,#f4f5f7 50%,#fafafa 100%)}
.touch-title{left:0;width:1200px;top:2018px;text-align:center}
.field{border:1px solid var(--line);background:rgba(255,255,255,.7);font-size:16px;color:var(--muted);padding:17px 15px}
.form-foot{left:226px;top:2406px;width:748px;height:50px;display:flex;align-items:center;justify-content:space-between}
.forgot{padding-left:15px;font-size:16px;color:var(--muted)}
.send{width:364px;height:50px;background:var(--blue);color:#fff;display:flex;align-items:center;justify-content:center;font-size:18px}

/* footer */
.site-footer{left:0;top:2560px;width:1200px;height:286px;background:linear-gradient(180deg,#0b58a8,#0a4f98);color:#fff}
.contact-item{position:absolute;top:66px;width:320px;text-align:center;font-size:16px;line-height:23px}
.contact-item .icon{width:54px;height:54px;border:1.5px solid #fff;border-radius:50%;margin:0 auto 10px;display:flex;align-items:center;justify-content:center}
.contact-item h3{font-weight:500;font-size:16px;margin-bottom:6px}
.copyright{position:absolute;left:0;width:1200px;top:232px;text-align:center;font-size:16px}
</style>
</head>
<body>

<header class="site-header">
  <div class="brand"><span class="brand-mark"></span><span class="brand-name">VEL-CORA<small>SOLUTIONS</small></span></div>
  <nav class="main-nav">
    <a class="active" style="left:0">HOME</a>
    <a style="left:80px">ABOUT</a>
    <a style="left:168px">SERVICES</a>
    <a style="left:276px">TEAMS</a>
    <a style="left:363px">NEWS</a>
    <a style="left:445px">CONTACT</a>
  </nav>
  <a class="btn login abs">
    <svg width="14" height="16" viewBox="0 0 14 16"><circle cx="7" cy="4.5" r="3.8" fill="#fff"/><path d="M0 16c0-5 3-7 7-7s7 2 7 7z" fill="#fff"/></svg>LOGIN
  </a>
</header>

<div class="hero-photo abs" role="img" aria-label="Business people reviewing financial charts at a desk"></div>
<svg class="abs" style="left:0;top:600px" width="1200" height="260" viewBox="0 600 1200 260">
  <path d="M0 670 C 120 625, 250 610, 420 650 S 800 770, 972 757 S 1150 700, 1200 663 L1200 860 L0 860 Z" fill="#fff"/>
  <path d="M0 670 C 120 625, 250 610, 420 650 S 800 770, 972 757 S 1150 700, 1200 663" fill="none" stroke="#8cc63f" stroke-width="6"/>
</svg>
<div class="hero-box abs">
  <h1>VEL-CORA SOLUTIONS</h1>
  <p>Vel Cora is an investment company put together by a group of seasoned business professionals who have come together</p>
</div>
<a class="btn get-started abs">GET STARTED</a>
<div class="dots abs"><span></span><span></span><span class="on"></span><span></span><span></span></div>

<section>
  <div class="about-bg abs" style="top:860px;height:496px"></div>
  <svg class="about-ring abs" width="400" height="400" viewBox="0 0 400 400"><path d="M200 7 A193 193 0 0 0 200 393" fill="none" stroke="#8cc63f" stroke-width="5"/></svg>
  <div class="about-photo abs" role="img" aria-label="Hand pointing at bar charts on a tablet"></div>
  <h2 class="section-title about-title abs">ABOUT US</h2>
  <p class="about-text abs">Vel Cora is an investment company put together by a group of seasoned business professionals who have come together to combine decades of success in the real estate development, management, financing and medical services. The company will be a full service company offering turn key solutions for medical professionals.</p>
  <a class="btn read-more abs">READ MORE</a>
</section>

<section class="services abs"></section>
<h2 class="section-title services-title abs">OUR SERVICES</h2>
<svg class="arrow abs" style="left:66px" viewBox="0 0 38 38"><circle cx="19" cy="19" r="18" fill="#fff" stroke="#555"/><path d="M22 11 L14 19 L22 27" fill="none" stroke="#555" stroke-width="1.5"/></svg>
<svg class="arrow abs" style="left:1095px" viewBox="0 0 38 38"><circle cx="19" cy="19" r="18" fill="#fff" stroke="#555"/><path d="M16 11 L24 19 L16 27" fill="none" stroke="#555" stroke-width="1.5"/></svg>
<div class="service-card card-estate abs" role="img" aria-label="Real estate agreement with a small house model"></div>
<div class="service-card card-mgmt abs" role="img" aria-label="Manager reviewing charts on a tablet"></div>
<div class="service-card card-finance abs" role="img" aria-label="Stethoscope on medical billing forms"></div>
<p class="service-label abs" style="left:110px">REAL ESTATE DEVELOPMENT</p>
<p class="service-label abs" style="left:440px">MANAGEMENT</p>
<p class="service-label abs" style="left:770px">FINANCING AND MEDICAL SERVICES</p>

<section>
  <div class="contact-bg abs"></div>
  <h2 class="section-title touch-title abs">GET IN TOUCH</h2>
  <div class="field abs" style="left:226px;top:2097px;width:366px;height:52px">First Name</div>
  <div class="field abs" style="left:608px;top:2097px;width:366px;height:52px">Last Name</div>
  <div class="field abs" style="left:226px;top:2163px;width:366px;height:52px">Email</div>
  <div class="field abs" style="left:608px;top:2163px;width:366px;height:52px">Phone</div>
  <div class="field abs" style="left:226px;top:2232px;width:748px;height:154px">Message</div>
  <div class="form-foot abs">
    <p class="forgot">Forgot your password?</p>
    <a class="send">SEND</a>
  </div>
</section>

<footer class="site-footer abs">
  <div class="contact-item" style="left:150px">
    <div class="icon"><svg width="22" height="22" viewBox="0 0 24 24"><path d="M5 3l4 1 1 5-2 1.5c1 2.5 3 4.5 5.5 5.5L15 14l5 1 1 4-2 2C10 21 3 14 3 5z" fill="none" stroke="#fff" stroke-width="1.5"/></svg></div>
    <h3>PHONE</h3><p>888-888-8888</p>
  </div>
  <div class="contact-item" style="left:441px">
    <div class="icon"><svg width="20" height="24" viewBox="0 0 20 24"><path d="M10 23C4 15 2 12 2 8a8 8 0 0 1 16 0c0 4-2 7-8 15z" fill="#fff"/><circle cx="10" cy="8" r="3" fill="#0b58a8"/></svg></div>
    <h3>ADDRESS</h3><p>Nemo enim ipsam<br>voluptatem quia voluptas sit</p>
  </div>
  <div class="contact-item" style="left:764px">
    <div class="icon"><svg width="22" height="16" viewBox="0 0 22 16"><rect x="1" y="1" width="20" height="14" fill="none" stroke="#fff" stroke-width="1.5"/><path d="M1 1l10 8 10-8" fill="none" stroke="#fff" stroke-width="1.5"/></svg></div>
    <h3>EMAIL</h3><p>info@velcorasolutions.com</p>
  </div>
  <p class="copyright">© 2020 All Rights Reserved</p>
</footer>

</body>
</html>
```